Trailer Lettering or Partial Wrap

I purchased a new gloss black 7' wide x 12' long x 7' height enclosed cargo trailer that I would like to brand for advertising. on all 4 sides. Our font is AgencyFB (and we only use lower case letters). To reduce cost I thought using the black gloss background could be achieved and use cut out vinyl rather than full wrap unless there are some other ideas. Our colors are Black, White, and Red (HEX #BE1E2D. Items to be displayed:
- logo
- phone # (405) 555-2716
- email. catering@kelpcornerok.com
- web address: www.kelpcornerok.com
- our 2 restaurant locations
- "Edmond" 4875 NE 92nd, Edmond OK 73099
- "NW-OKC" 2719 E Larkspur Ave, Oklahoma City, OK 73198

we would also like to highlight 3 services we offer:
- Catering
- Rent-A-Chef Events
- Sushi Making Classes

For reference our chopsticks from the logo files we use on a lot of print items. Not that I want it to be like this, but I did attach a sample of what ChatGPT created though is in an unusable format and fonts aren't consistent. As well a recent 2' x 4' sign we had made to use on table displays.

We also do like the wording on that last item of " Sushi | Experience | Elevated"

```html
<!DOCTYPE html>
<html lang="en">
<head>
<meta charset="utf-8">
<title>Kelp Corner – Trailer Side Lettering</title>
<link href="https://fonts.googleapis.com/css2?family=Saira+Condensed:wght@300;400;600&display=swap" rel="stylesheet">
<style>
  :root {
    --gloss-black: #0b0b0c;
    --panel-seam: #26272a;
    --brand-red: #be1e2d;
    --vinyl-white: #f2f2f2;
    --logo-grey: #d6d6d6;
    --trim-silver: #c9ccd0;
    --backdrop: #e6e7e9;
    --type: "Saira Condensed", "Arial Narrow", sans-serif;
  }
  * { box-sizing: border-box; margin: 0; padding: 0; }
  html, body { width: 1200px; height: 900px; overflow: hidden; background: var(--backdrop); }
  body { position: relative; font-family: var(--type); }

  .trailer-side {
    position: absolute; left: 30px; top: 100px; width: 1140px; height: 700px;
    background: var(--gloss-black);
    border-top: 10px solid var(--trim-silver);
    border-bottom: 8px solid var(--trim-silver);
    overflow: hidden;
  }
  .seam { position: absolute; top: 0; bottom: 0; width: 2px; background: var(--panel-seam); }
  .seam--one { left: 374px; }
  .seam--two { left: 757px; }

  .brand-name {
    position: absolute; left: 80px; top: 60px;
    font-family: var(--type); font-weight: 600; color: var(--logo-grey);
    font-size: 150px; line-height: 0.92; letter-spacing: -2px; text-transform: lowercase;
  }

  .services { position: absolute; left: 466px; top: 58px; width: 272px; }
  .service { position: absolute; left: 0; width: 272px; display: flex; align-items: center; gap: 16px; }
  .service--catering { top: 8px; }
  .service--chef { top: 142px; }
  .service--classes { top: 279px; }
  .service__icon { width: 84px; height: 84px; flex: none; }
  .service__label {
    color: var(--vinyl-white); font-weight: 400; font-size: 30px; line-height: 1.1;
    text-transform: uppercase; letter-spacing: 0.5px;
  }
  .service-divider { position: absolute; left: 466px; width: 272px; height: 2px; background: var(--brand-red); }
  .service-divider--first { top: 172px; }
  .service-divider--second { top: 307px; }

  .tagline-band {
    position: absolute; left: 0; top: 446px; width: 785px; height: 36px;
    background: var(--vinyl-white);
    display: flex; align-items: center; justify-content: center; gap: 12px;
    padding-left: 40px;
    font-size: 23px; font-weight: 400; text-transform: uppercase; color: var(--gloss-black);
  }
  .tagline-band .accent { color: var(--brand-red); }
  .web-band {
    position: absolute; left: 0; top: 482px; width: 785px; height: 58px;
    background: var(--brand-red);
    display: flex; align-items: center; justify-content: center; padding-left: 40px;
    color: var(--vinyl-white); font-size: 40px; font-weight: 400; letter-spacing: 3px; text-transform: uppercase;
  }

  .door {
    position: absolute; left: 785px; top: 76px; width: 320px; height: 596px;
    border: 14px solid var(--trim-silver);
    outline: 3px solid #8e9196;
    background: var(--gloss-black);
  }
  .location { position: absolute; left: 0; width: 100%; text-align: center; color: var(--vinyl-white); }
  .location--edmond { top: 100px; }
  .location--okc { top: 360px; }
  .location__pin { display: block; margin: 0 auto 4px; width: 28px; height: 38px; }
  .location__city { font-size: 52px; font-weight: 400; line-height: 1; text-transform: uppercase; }
  .location__rule { width: 122px; height: 2px; background: var(--brand-red); margin: 8px auto 10px; }
  .location__address { font-size: 22px; font-weight: 300; line-height: 1.25; }
</style>
</head>
<body>
  <main class="trailer-side">
    <div class="seam seam--one"></div>
    <div class="seam seam--two"></div>

    <h1 class="brand-name">kelp<br>corner</h1>

    <section class="services">
      <div class="service service--catering">
        <svg class="service__icon" viewBox="0 0 84 84" role="img" aria-label="Chef hat and knife icon for catering">
          <circle cx="42" cy="42" r="37" fill="none" stroke="#be1e2d" stroke-width="5"/>
          <circle cx="42" cy="42" r="26" fill="#2a2b2e"/>
        </svg>
        <span class="service__label">Catering</span>
      </div>
      <div class="service service--chef">
        <svg class="service__icon" viewBox="0 0 84 84" role="img" aria-label="Sushi roll icon for rent-a-chef events">
          <circle cx="42" cy="42" r="37" fill="none" stroke="#be1e2d" stroke-width="5"/>
          <circle cx="42" cy="42" r="26" fill="#2a2b2e"/>
        </svg>
        <span class="service__label">Rent-a-Chef<br>Events</span>
      </div>
      <div class="service service--classes">
        <svg class="service__icon" viewBox="0 0 84 84" role="img" aria-label="Sushi on serving board icon for sushi making classes">
          <circle cx="42" cy="42" r="37" fill="none" stroke="#be1e2d" stroke-width="5"/>
          <circle cx="42" cy="42" r="26" fill="#2a2b2e"/>
        </svg>
        <span class="service__label">Sushi Making<br>Classes</span>
      </div>
    </section>
    <div class="service-divider service-divider--first"></div>
    <div class="service-divider service-divider--second"></div>

    <div class="tagline-band">
      <span class="accent">Sushi</span><span>|</span><span>Experience</span><span>|</span><span class="accent">Elevated</span>
    </div>
    <div class="web-band">www.kelpcornerok.com</div>

    <section class="door">
      <div class="location location--edmond">
        <svg class="location__pin" viewBox="0 0 28 38" aria-hidden="true">
          <path d="M14 0C6.3 0 0 6.1 0 13.7 0 24 14 38 14 38s14-14 14-24.3C28 6.1 21.7 0 14 0z" fill="#be1e2d"/>
          <circle cx="14" cy="13.5" r="5.5" fill="#0b0b0c"/>
        </svg>
        <div class="location__city">Edmond</div>
        <div class="location__rule"></div>
        <p class="location__address">4875 NE 92nd<br>Edmond, OK 73099</p>
      </div>
      <div class="location location--okc">
        <svg class="location__pin" viewBox="0 0 28 38" aria-hidden="true">
          <path d="M14 0C6.3 0 0 6.1 0 13.7 0 24 14 38 14 38s14-14 14-24.3C28 6.1 21.7 0 14 0z" fill="#be1e2d"/>
          <circle cx="14" cy="13.5" r="5.5" fill="#0b0b0c"/>
        </svg>
        <div class="location__city">NW-OKC</div>
        <div class="location__rule"></div>
        <p class="location__address">2719 E Larkspur Ave<br>Oklahoma City, OK 73198</p>
      </div>
    </section>
  </main>
</body>
</html>
```